Event Center Website

We need a new website design for an upscale event center in Reno, Nevada. The building hosts everything from weddings to corporate events to funerals and it competitively more expensive. The overall look and feel is consistent with a Lake Tahoe aesthetic. The current site can be viewed at www.themaplehallevents.com. They are looking for a major upgrade. A sample site they like is www.cliffsidelodgestay.com. We have new photography available (some attached). The site should be very visual. A site map is attached as well for direction on what elements the site should include as well as labels for navigation. I am looking for a home page and sample interior page. Any questions, let me know. Thanks.
Updates

I have added some photography of the center itself for use rather than stock photography. Thanks!

Target Market(s)

Brides, professionals, high-income

Industry/Entity Type

Building

Requirements
Must have
• See site map

```html
<!DOCTYPE html>
<html lang="en">
<head>
<meta charset="utf-8">
<title>Maple Hall – Meet Our Team</title>
<link rel="stylesheet" href="https://fonts.googleapis.com/css2?family=Ubuntu:wght@400;500&display=swap">
<style>
:root{
  --cream:#f5e6c4;
  --cream-panel:rgba(246,232,200,0.9);
  --brown-dark:#4a2614;
  --brown:#5a3220;
  --brown-text:#4a2a18;
  --rust:#9a4a25;
  --orange:#c8671a;
  --email-bg:#7e4009;
  --contact-bg:#3f1f0c;
  --white:#ffffff;
}
*{margin:0;padding:0;box-sizing:border-box}
html,body{width:1200px;height:874px;overflow:hidden;background:var(--cream)}
body{font-family:"Ubuntu",sans-serif;color:var(--brown-text);position:relative}
.hero{position:absolute;left:0;top:0;width:1200px;height:708px;
  background:
    radial-gradient(ellipse at 50% 20%,#f4c77a 0%,#c8843a 25%,transparent 55%),
    linear-gradient(180deg,#6b4422 0%,#9a6a3a 30%,#d9c4a8 55%,#8c7a70 75%,#3a2a26 100%)}
.top-links{position:absolute;left:849px;top:0;width:227px;height:52px;background:var(--brown);
  display:flex;align-items:center;justify-content:center;gap:13px;color:var(--white);font-size:15px}
.top-links .sep{width:2px;height:26px;background:var(--white)}
.main-nav{position:absolute;left:100px;top:52px;width:976px;height:58px;background:var(--cream);display:flex;align-items:center}
.brand{display:flex;align-items:center;gap:8px;width:200px;padding-left:8px;font-size:22px;font-weight:500;color:var(--brown-dark)}
.brand .dot{width:12px;height:12px;border-radius:50%;background:var(--brown-dark)}
.main-nav ul{list-style:none;display:flex;gap:34px;margin-left:11px}
.main-nav li{font-size:14.5px;font-weight:500;color:var(--brown-dark);position:relative;height:58px;line-height:58px}
.main-nav li.active::after{content:"";position:absolute;left:-3px;right:-3px;bottom:0;height:2px;background:var(--rust)}
.arrow{position:absolute;top:387px;width:46px;height:46px;border-radius:50%;background:var(--rust)}
.arrow.prev{left:22px}.arrow.next{left:1129px}
.team-panel{position:absolute;left:212px;top:188px;width:794px;height:405px;background:var(--cream-panel)}
.team-panel h1{font-size:26px;font-weight:500;text-align:center;color:var(--brown);line-height:50px;border-bottom:1px solid var(--brown);height:50px}
.close{position:absolute;left:762px;top:17px;width:22px;height:22px}
.member-name{font-size:26px;font-weight:500;text-align:center;margin-top:8px;color:var(--brown)}
.member-name span,.caption span{color:var(--orange)}
.portrait{position:absolute;left:27px;top:103px;width:236px;height:221px;border:3px solid #7a5a45;background:linear-gradient(180deg,#f7f5f2,#d9c2a8 60%,#9aa4ad)}
.caption{position:absolute;left:27px;top:336px;width:236px;text-align:center;font-size:16px;font-weight:500;color:var(--brown)}
.bio{position:absolute;left:283px;top:99px;width:468px;font-size:13.7px;line-height:22.3px;text-align:justify;color:var(--brown-text)}
.newsletter{position:absolute;left:131px;top:747px;width:339px;height:60px;background:var(--email-bg);display:flex;align-items:center;color:var(--white)}
.newsletter .field{flex:1;padding-left:9px;font-size:14.5px}
.newsletter .send{width:55px;height:60px;background:var(--orange);display:flex;align-items:center;justify-content:center;font-size:14.5px}
.contact{position:absolute;left:495px;top:748px;width:362px;height:58px;background:var(--contact-bg);display:flex;color:var(--white);font-size:13px;line-height:23px}
.contact .address{width:150px;padding:8px 0 0 11px;border-right:1px solid #6a4a35}
.contact .lines{padding:6px 0 0 9px}
.contact .lines span{color:var(--orange);margin-right:4px}
.social{position:absolute;left:887px;top:748px;width:189px;height:60px;background:var(--brown);display:flex;align-items:center;padding-left:20px;gap:11px}
.social span{width:29px;height:29px;display:block}
.footer-nav{position:absolute;left:0;top:834px;width:1200px;display:flex;justify-content:center;gap:28px;list-style:none;font-size:14px;color:var(--brown-dark)}
</style>
</head>
<body>
<div class="hero" role="img" aria-label="Photo of the event hall interior with draped ceiling, chandelier, and rows of chairs along an aisle"></div>

<div class="top-links"><span>FAQ</span><span class="sep"></span><span>TESTIMONIAL</span></div>

<nav class="main-nav">
  <div class="brand"><span class="dot"></span>Maple Hall</div>
  <ul>
    <li class="active">ABOUT US</li><li>GALLERY</li><li>WEDDING</li><li>MEETINGS</li><li>OTHER EVENTS</li><li>CATERING</li><li>MENUS</li>
  </ul>
</nav>

<svg class="arrow prev" viewBox="0 0 46 46"><path d="M24 15 L16 23 L24 31 M31 15 L23 23 L31 31" fill="none" stroke="#fff" stroke-width="2.5"/></svg>
<svg class="arrow next" viewBox="0 0 46 46"><path d="M15 15 L23 23 L15 31 M22 15 L30 23 L22 31" fill="none" stroke="#fff" stroke-width="2.5"/></svg>

<section class="team-panel">
  <h1>MEET OUR TEAM</h1>
  <svg class="close" viewBox="0 0 22 22"><circle cx="11" cy="11" r="11" fill="#4a2a18"/><path d="M7 7 L15 15 M15 7 L7 15" stroke="#fff" stroke-width="2.5"/></svg>
  <h2 class="member-name">Marcus, <span>Chef</span></h2>
  <div class="portrait" role="img" aria-label="Portrait photo of the chef"></div>
  <p class="caption">Marcus, <span>Chef</span></p>
  <p class="bio">Never intending to become a Chef, Marcus began his career at a part-time job in the Pinebrook kitchen. He was immediately drawn in by the excitement of the profession, enjoying the camaraderie, the adrenaline, the rush, the pace, and the noise of the kitchen. From there, Marcus went to work at the Summit Crest Resort in Lake Tahoe to round out his culinary education. He had the privilege of working with Golden Ladle Award winning chefs, and learned how to execute the finer points of upscale dining. A Reno native, Marcus returned to Northern Nevada bringing his excellent background to Maple Hall. He was recently married to his beautiful wife, Elena.</p>
</section>

<form class="newsletter">
  <div class="field">ENTER YOUR EMAIL</div>
  <svg width="32" height="28" viewBox="0 0 32 28" style="margin-right:12px"><rect x="1" y="9" width="30" height="18" fill="none" stroke="#fff" stroke-width="1.5"/><path d="M1 9 L16 20 L31 9" fill="none" stroke="#fff" stroke-width="1.5"/></svg>
  <div class="send">SEND</div>
</form>

<address class="contact" style="font-style:normal">
  <div class="address">48 Ridgeline Avenue<br>Reno, NV 89502</div>
  <div class="lines"><div><span>Phone:</span>775-555-0142</div><div><span>Email:</span>info@themaplehallevents.com</div></div>
</address>

<div class="social">
  <span style="background:#3b5998"></span><span style="background:#2aa9e0"></span><span style="background:#d0312d"></span><span style="background:#f26522"></span>
</div>

<ul class="footer-nav">
  <li>ABOUT US</li><li>GALLERY</li><li>WEDDING</li><li>MEETINGS</li><li>OTHER EVENTS</li><li>CATERING</li><li>MENUS</li>
</ul>
</body>
</html>
```